KV HOLDING Business Cards

I need business cards for "KV Holding group LLC" doublesided... logo on the back (also include logo on front)
logo attached to project... i have jpg up..
Company Info:
827 North Cadwell Avenue, Suite 4B
Chicago, Illinois 60654
facsimile 312-481-2075 (list fax, address, website on all cards.)
www.kvholdinggroup.example
Three different people on cards:
Darnell P. Okafor, CPA MST
Principal
ofc 312-481-3900
mobile 312-204-7751
darnellpokafor@kvholdinggroup.example
Hollis T. Brennecke, CPA MST
Principal
hollistbrennecke@kvholdinggroup.example
mobile 708-539-1184
ofc 312-481-3900
Conrad M Pavlik
Principal
ofc 312-481-3900
no mobile
conradmpavlik@kvholdinggroup.example
I have multiple projects listed.. see below:
Business cards for amber gate ventures llc
letterhead
envelopes
Business cards for KV Holding LLC
letterhead
envelopes
Target Market(s)
rich people
Industry/Entity Type
Business
Look and feel
Each slider illustrates characteristics of the customer's brand and the style your logo design should communicate.

```html
<!DOCTYPE html>
<html lang="en">
<head>
<meta charset="utf-8">
<title>KV Holding Group – Business Cards</title>
<link rel="stylesheet" href="https://fonts.googleapis.com/css2?family=Exo+2:wght@500&display=swap">
<style>
  :root {
    --bg: #ecebe8;
    --card-white: #ffffff;
    --band-grey: #a6a6a6;
    --navy: #0b4a80;
    --navy-text: #114a7c;
    --on-navy: #ffffff;
    --shadow: rgba(0, 0, 0, 0.18);
  }
  * { margin: 0; padding: 0; box-sizing: border-box; }
  html, body {
    width: 1200px; height: 658px; overflow: hidden;
    background: var(--bg);
    font-family: "Exo 2", Arial, sans-serif;
    font-weight: 500;
  }
  .stage {
    position: relative; width: 1200px; height: 658px;
    display: flex; align-items: center; justify-content: center; gap: 40px;
  }
  .card {
    position: relative; width: 540px; height: 320px;
    background: var(--card-white);
    box-shadow: 0 6px 18px var(--shadow);
    overflow: hidden;
  }
  /* Back of card */
  .card-back .band {
    position: absolute; left: 0; right: 0; height: 52px; background: var(--band-grey);
  }
  .card-back .band-top { top: 0; }
  .card-back .band-bottom { bottom: 0; }
  .brand {
    display: flex; flex-direction: column; align-items: center;
    color: var(--navy-text);
  }
  .brand-dot {
    width: 34px; height: 34px; border-radius: 50%; background: var(--navy-text);
  }
  .brand-name { letter-spacing: 0.02em; white-space: nowrap; }
  .card-back .brand {
    position: absolute; left: 0; right: 0; top: 112px; gap: 14px;
  }
  .card-back .brand-name { font-size: 30px; }
  /* Front of card */
  .card-front { display: flex; }
  .front-info {
    width: 56%; padding: 58px 18px 0 22px;
    color: var(--navy-text);
  }
  .front-info .brand { gap: 10px; }
  .front-info .brand-dot { width: 26px; height: 26px; }
  .front-info .brand-name { font-size: 21px; }
  .address {
    margin-top: 22px; text-align: center;
    font-size: 10.5px; line-height: 1.35;
  }
  .front-people {
    width: 44%; background: var(--navy); color: var(--on-navy);
    padding: 34px 20px 0 10px; text-align: right;
    font-size: 11.5px; line-height: 1.28;
  }
  .person + .person { margin-top: 22px; }
  .person-name { font-size: 12.5px; }
</style>
</head>
<body>
  <main class="stage">
    <section class="card card-back" aria-label="Card back">
      <div class="band band-top"></div>
      <div class="brand">
        <span class="brand-dot"></span>
        <span class="brand-name">KV Holding Group LLC</span>
      </div>
      <div class="band band-bottom"></div>
    </section>

    <section class="card card-front" aria-label="Card front">
      <div class="front-info">
        <div class="brand">
          <span class="brand-dot"></span>
          <span class="brand-name">KV Holding Group LLC</span>
        </div>
        <p class="address">
          827 North Cadwell Avenue, Suite 4B<br>
          Chicago, Illinois 60654<br>
          facsimile 312-481-2075<br>
          www.kvholdinggroup.example
        </p>
      </div>
      <div class="front-people">
        <div class="person">
          <p class="person-name">Darnell P. Okafor, CPA MST</p>
          <p>Principal</p>
          <p>Ofc 312-481-3900</p>
          <p>Mobile 312-204-7751</p>
          <p>darnellpokafor@kvholdinggroup.example</p>
        </div>
        <div class="person">
          <p class="person-name">Hollis T. Brennecke, CPA MST</p>
          <p>Principal</p>
          <p>hollistbrennecke@kvholdinggroup.example</p>
          <p>mobile 708-539-1184</p>
          <p>ofc 312-481-3900</p>
        </div>
        <div class="person">
          <p class="person-name">Conrad M Pavlik</p>
          <p>Principal</p>
          <p>ofc 312-481-3900</p>
          <p>conradmpavlik@kvholdinggroup.example</p>
        </div>
      </div>
    </section>
  </main>
</body>
</html>
```